A new presentation to our clients

we are a Real Estate agency, our website is www.lumibrasa.com and it’s time to have a new, fashion and remarcable Business Card. we want to differentiate ourselves from other companies so we want a business card that differentiates us. we want the business card to impact our customers. in the competitive market that we have today, we have to be different and it is this difference that we seek

Target Market(s)

Real Estate Clients

Contact Information for Business Card

We search a totaly diferent card from the usual

Font styles to use
Sans Serif

Colors
e34197

Requirements
Must have
• Logo, adress, phone contact, e-mail, photo, and our website
Nice to have
• We would like to see a modern business card
Should not have
• Houses or building draws

```html
<!DOCTYPE html>
<html lang="en">
<head>
<meta charset="utf-8">
<title>Lumi Brasa – Business Card</title>
<link rel="stylesheet" href="https://fonts.googleapis.com/css2?family=Open+Sans:wght@400;600&family=Oswald:wght@500&display=swap">
<style>
  :root {
    --brand-pink: #e34197;
    --brand-pink-deep: #d01a6c;
    --ink: #4a4a4a;
    --paper: #ffffff;
    --backdrop: #ecebea;
  }
  * { margin: 0; padding: 0; box-sizing: border-box; }
  html, body { width: 1200px; height: 900px; overflow: hidden; }
  body {
    background: var(--backdrop);
    font-family: "Open Sans", Arial, sans-serif;
    position: relative;
  }
  .card {
    position: absolute;
    left: 285px;
    width: 630px;
    height: 360px;
    border-radius: 4px;
    box-shadow: 0 6px 18px rgba(0,0,0,.15);
    overflow: hidden;
  }
  .card--front {
    top: 70px;
    background: linear-gradient(160deg, var(--brand-pink-deep), var(--brand-pink));
    display: flex; align-items: center; justify-content: center;
  }
  .card--back { top: 470px; background: var(--paper); }
  .brand-name {
    font-family: "Open Sans", Arial, sans-serif;
    font-weight: 600;
    letter-spacing: 1px;
  }
  .card--front .brand-name { color: var(--paper); font-size: 64px; }
  .card--back .brand-name {
    position: absolute; top: 58px; left: 0; right: 0;
    text-align: center; color: var(--brand-pink); font-size: 40px;
  }
  .identity {
    position: absolute; top: 170px; right: 342px; text-align: right;
  }
  .identity__name {
    font-family: "Oswald", "Arial Narrow", sans-serif;
    font-weight: 500; font-size: 36px; line-height: 1;
    color: var(--brand-pink); text-transform: uppercase;
  }
  .identity__role { font-size: 17px; color: var(--ink); margin-top: -2px; }
  .divider {
    position: absolute; top: 162px; left: 306px;
    width: 2px; height: 66px; background: var(--brand-pink);
  }
  .contact-list {
    position: absolute; top: 158px; left: 328px; list-style: none;
  }
  .contact-list li {
    display: flex; align-items: center; gap: 10px;
    font-size: 17px; color: var(--ink); line-height: 25px;
  }
  .icon { width: 16px; height: 16px; flex: none; }
  .address {
    position: absolute; bottom: 42px; left: 0; right: 0;
    display: flex; justify-content: center; align-items: center; gap: 10px;
    font-size: 17px; color: var(--ink);
  }
</style>
</head>
<body>
  <section class="card card--front">
    <span class="brand-name">Lumi Brasa</span>
  </section>

  <section class="card card--back">
    <span class="brand-name">Lumi Brasa</span>

    <div class="identity">
      <div class="identity__name">Marcus Hale</div>
      <div class="identity__role">President</div>
    </div>
    <div class="divider"></div>

    <ul class="contact-list">
      <li>
        <svg class="icon" viewBox="0 0 16 16"><path fill="#e34197" d="M3.5 1.5l2.5 0 1 3.5-1.8 1.3a8 8 0 0 0 4.5 4.5L11 9l3.5 1v2.5c0 1-1 2-2 2C6.5 14.5 1.5 9.5 1.5 3.5c0-1 1-2 2-2z"/></svg>
        00 4321 765 999
      </li>
      <li>
        <svg class="icon" viewBox="0 0 16 16"><rect x="1" y="3" width="14" height="10" rx="1" fill="#e34197"/><path d="M1.5 4l6.5 5 6.5-5" fill="none" stroke="#fff" stroke-width="1.3"/></svg>
        yourmail@lumibrasa.com
      </li>
      <li>
        <svg class="icon" viewBox="0 0 16 16"><circle cx="8" cy="8" r="6.5" fill="none" stroke="#e34197" stroke-width="1.6"/><ellipse cx="8" cy="8" rx="2.8" ry="6.5" fill="none" stroke="#e34197" stroke-width="1.3"/><path d="M1.5 8h13M2.5 5h11M2.5 11h11" stroke="#e34197" stroke-width="1.2"/></svg>
        www.lumibrasa.com
      </li>
    </ul>

    <div class="address">
      <svg class="icon" viewBox="0 0 16 16"><path fill="#e34197" d="M8 0.8a5 5 0 0 0-5 5c0 3.8 5 9.6 5 9.6s5-5.8 5-9.6a5 5 0 0 0-5-5z"/><circle cx="8" cy="5.8" r="1.9" fill="#fff"/></svg>
      West 18th Avenue, Suite 310, Denver, CO 80204
    </div>
  </section>
</body>
</html>
```